Logo & Visitenkarte für Weinbauer
Zielgruppe
Ich bin Weinbauer und betreibe auch einen Buschenschank. Zielgruppe ist die Gastronomie und der (Durchschnitts-) Endverbraucher.
Aufgabenstellung
Unsere Betriebsstätte ist im Rebhügelgau Weinviertel (Österreich).
Wir wollen die Werte Tradition, Regional, Vertrauen und Bodenständigkeit vermitteln.
Unsere Kunden schätzen die Herkunft.
Das Logo soll als Firmenlogo und auch für die Weinetiketten verwendet werden können.

```html
<!DOCTYPE html>
<html lang="de">
<head>
<meta charset="utf-8">
<title>Weinbau Brunner – Visitenkarte</title>
<link rel="stylesheet" href="https://fonts.googleapis.com/css2?family=Oswald:wght@300&display=swap">
<style>
  :root {
    --backdrop: #dcebf1;
    --card: #c8d0a0;
    --card-light: #d3dab0;
    --ink: #2b2d27;
  }
  * { margin: 0; padding: 0; box-sizing: border-box; }
  html, body {
    width: 1200px;
    height: 900px;
    overflow: hidden;
    background: var(--backdrop);
  }
  .stage {
    width: 1200px;
    height: 900px;
    display: flex;
    align-items: center;
    justify-content: center;
    gap: 60px;
  }
  .card {
    width: 440px;
    height: 286px;
    background: linear-gradient(160deg, var(--card-light), var(--card));
    display: flex;
    align-items: center;
    justify-content: center;
    color: var(--ink);
    font-family: "Oswald", sans-serif;
    font-weight: 300;
    text-transform: uppercase;
  }
  .brand-name {
    font-size: 22px;
    letter-spacing: 0.14em;
    white-space: nowrap;
  }
  .address {
    font-style: normal;
    font-size: 17px;
    letter-spacing: 0.12em;
    line-height: 1.45;
  }
</style>
</head>
<body>
  <main class="stage">
    <section class="card card-front">
      <p class="brand-name">Weinbau Brunner</p>
    </section>
    <section class="card card-back">
      <address class="address">
        Musterweg 1<br>
        Rebhügelgau<br>
        Österreich
      </address>
    </section>
  </main>
</body>
</html>
```